Application for baby milk and water counter

We are building baby food app. Need to design main screen for tha app first so we can go forward to other secondary screens of the app

Food dashboard screen
Food dashboard screen is main page for view/edit food data

General vision
I see the app in pastel colors with some illustrations to make the app more in positive. You can influence from game Glimmer Tides. I see with smooth colors and gradients like in a game. Also need to have animations/transitions for each action. Each click should create smooth transition to new state. My idea is to build one dashboard screen for food which we can reuse it for other screens. So a lot of thinking should go into design stage to app appealing.

Food Dashboard
Current screen should show all the data about food intake of the baby. So here user should see

Milk How much food baby had in ml/oz. So there should be some kind of illustrated bottle or glass or smth that shows it is filled with that amount.

Add/Remove controls for food. Should be some kind of custom control for inputing amount to remove/add. I see it as a slider on the side of the bottle. User slides up or down and amount is added/removed.

Notification. So user should be aware how many hours/minutes left for next food intake. This is optional field, so consider it could be disabled. So no empty space should be on a screen. There should be human readable text. Something like. 1:30 minutes left for next intake. Maybe could be some custom made icons to illustrate that it is next food intake.

Burped: User should have ability to how much baby burped. This amount is integer value. So it could be “Baby burped 2 times today”. So again here I see some custom made/icon to illustrate how many times baby burped and amount next to it. I see changing the value just by tapping, but I don’t know how to edit if user tapped accidentally more than it should be. So TBD here.

Date and time: Dashboard should show for which date it is viewing/editing data. Should be able to change it, so user can add/edit data for yesterday. Don’t want to see here calendar on a screen so need to come up with nice design decision.

Water: User should have ability to view/edit water intake of the baby, but water is secondary information so it should be smaller than milk, or come up with some other idea how to show the water. I see to have same controls for water like for milk. Water intake is optional it can be disabled by the user.

Target Market(s)

For just became mothers

Font styles to use
Sans Serif

Colors
0094D4
00A9DD
6FCCEA
C7EBF8
E9F6FB
FFC000
F8CF3A
FAE287
FDF2CF
FEFAEE
E54698
E96AAD
F1A4CE
F9D9EA
FCEFF6

Requirements
Must have
• Ilustrations or playfull icons for show information

```html
<!DOCTYPE html>
<html lang="en">
<head>
<meta charset="UTF-8">
<title>Baby Food</title>
<link rel="stylesheet" href="https://fonts.googleapis.com/css2?family=Barlow:wght@500;600;700;800&display=swap">
<style>
:root{
  --pink:#E96AAD;
  --pink-strong:#E54698;
  --pink-soft:#F9D9EA;
  --pink-pale:#FCEFF6;
  --pink-button:#FF6FB5;
  --ink:#111111;
  --muted:#B5B5B5;
  --card:#FFFFFF;
  --page:#F4F4F5;
}
*{box-sizing:border-box;margin:0;padding:0}
html,body{width:1200px;height:2560px;overflow:hidden}
body{font-family:"Barlow",sans-serif;background:var(--page);position:relative;color:var(--ink)}
.top-band{position:absolute;left:0;top:0;width:1200px;height:400px}
.sheet{position:absolute;left:0;top:224px;width:1200px;height:2336px;border-radius:64px 0 0 0;
  background:radial-gradient(ellipse at 80% 10%,#FFFFFF 0%,#F3F3F4 45%,#EDEDEE 100%)}
.title{position:absolute;left:112px;top:342px;font-size:88px;font-weight:700;letter-spacing:1px}
.card{position:absolute;background:var(--card);border-radius:20px;box-shadow:0 20px 60px rgba(0,0,0,.06)}
.time-card{left:99px;top:522px;width:979px;height:234px}
.time{position:absolute;left:48px;top:28px;font-size:90px;font-weight:600}
.date{position:absolute;left:64px;top:142px;font-size:35px;font-weight:500;color:var(--pink-strong)}
.toggle{position:absolute;left:819px;top:70px;width:115px;height:70px;border-radius:35px;background:var(--pink)}
.toggle::after{content:"";position:absolute;right:8px;top:8px;width:54px;height:54px;border-radius:50%;background:#fff}
.food-card{top:883px;width:454px;height:515px}
.milk-card{left:112px}
.water-card{left:624px}
.food-art{position:absolute;left:116px;top:96px;width:204px;height:204px;border-radius:50%;
  background:radial-gradient(circle at 50% 45%,var(--pink) 0%,var(--pink-soft) 55%,var(--pink-pale) 100%)}
.water-card .food-art{background:radial-gradient(circle at 50% 45%,#C7EBF8 0%,var(--pink-soft) 60%,var(--pink-pale) 100%)}
.food-name{position:absolute;left:0;width:100%;top:348px;text-align:center;font-size:46px;font-weight:700}
.food-amount{position:absolute;left:0;width:100%;top:412px;text-align:center;font-size:32px;font-weight:600;color:var(--muted)}
.add-btn{position:absolute;width:86px;height:86px;border-radius:50%;background:var(--pink-button)}
.add-btn svg{position:absolute;left:28px;top:28px}
.food-card .add-btn{left:344px;top:405px}
.burp-card{left:112px;top:1501px;width:967px;height:288px}
.burp-art{position:absolute;left:58px;top:61px;width:214px;height:150px;border-radius:40px;
  background:linear-gradient(160deg,#F8CF3A 0%,#FAE287 45%,#C7EBF8 100%)}
.burp-text{position:absolute;left:343px;top:80px;font-size:42px;font-weight:700;line-height:61px}
.burp-card .add-btn{left:840px;top:165px}
.next-intake{position:absolute;left:115px;top:2061px;width:967px;height:170px;border-radius:26px;
  background:var(--pink-button);color:#fff;font-size:42px;font-weight:700;display:flex;align-items:center;justify-content:center;letter-spacing:.5px}
</style>
</head>
<body>
<svg class="top-band" viewBox="0 0 1200 400" aria-hidden="true">
  <defs>
    <linearGradient id="bandGrad" x1="0" y1="0" x2="1" y2="0">
      <stop offset="0" stop-color="#F1A4CE"/>
      <stop offset="1" stop-color="#FF6FB5"/>
    </linearGradient>
  </defs>
  <path d="M0 0H1200V260H0Z" fill="url(#bandGrad)"/>
  <path d="M0 0C120 40 320 150 420 230H0Z" fill="#F4F4F5"/>
</svg>

<main class="sheet"></main>

<h1 class="title">BABY FOOD</h1>

<section class="card time-card">
  <div class="time">6:26 PM</div>
  <div class="date">31 05 2023</div>
  <div class="toggle" role="switch" aria-checked="true"></div>
</section>

<section class="card food-card milk-card">
  <div class="food-art" role="img" aria-label="Illustration of a pink baby milk bottle"></div>
  <div class="food-name">MILK</div>
  <div class="food-amount">200ML</div>
  <div class="add-btn"><svg width="30" height="30" viewBox="0 0 30 30"><path d="M15 3V27M3 15H27" stroke="#fff" stroke-width="6" stroke-linecap="round"/></svg></div>
</section>

<section class="card food-card water-card">
  <div class="food-art" role="img" aria-label="Illustration of a baby sippy cup with water"></div>
  <div class="food-name">WATER</div>
  <div class="food-amount">100ML</div>
  <div class="add-btn"><svg width="30" height="30" viewBox="0 0 30 30"><path d="M15 3V27M3 15H27" stroke="#fff" stroke-width="6" stroke-linecap="round"/></svg></div>
</section>

<section class="card burp-card">
  <div class="burp-art" role="img" aria-label="Illustration of a baby sleeping on a cloud"></div>
  <p class="burp-text">BABY BURPED 2 TIMES<br>TODAY</p>
  <div class="add-btn"><svg width="30" height="30" viewBox="0 0 30 30"><path d="M15 3V27M3 15H27" stroke="#fff" stroke-width="6" stroke-linecap="round"/></svg></div>
</section>

<div class="next-intake">2 HOURS LEFT FOR NEXT INTAKE</div>
</body>
</html>
```